Business Card for Multi-Brand Sportswear Company

We are looking for a business card which represents our company and the multiple brands within it.

The company: Fen Athletics (LTD)
The brands: Fen, TavaPuni, ElmStretch, Grit and Rain

Employees using these cards would be representing Fen Athletics, rather than any of the individual brands. You will see a current design within the uploaded files, to give some inspiration. The actual text of the brands is not necessary, but the logos should be on there is some format.

Our creative minds on this are stretched, so we are looking for someone to make this their own, and show us what a good business card should look like.

We may like to get these printed with spot gloss, so keep that in mind with your designs.

www.fenathletics.co.uk

Industry/Entity Type

Business

Contact Information for Business Card

Leo Pemberton-Hale
Operations Manager
(+44) 1632 960 418
Leo@fenathletics.co.uk
www.fenathletics.co.uk

Font styles to use
Sans Serif
Other font styles liked:
• Eurostile

Colors
ffffff

Requirements
Nice to have
• Dark (black) background

```html
<!DOCTYPE html>
<html lang="en">
<head>
<meta charset="utf-8">
<title>Fen Athletics Business Card</title>
<link rel="stylesheet" href="https://fonts.googleapis.com/css2?family=Saira:wght@400;500;700&display=swap">
<style>
  :root {
    --backdrop: #4a4a4a;
    --card-white: #ffffff;
    --brand-red: #ed1c24;
    --ink: #1a1a1a;
    --muted: #555555;
  }
  * { box-sizing: border-box; margin: 0; padding: 0; }
  html, body {
    width: 1105px; height: 1200px; overflow: hidden;
    background: var(--backdrop);
    font-family: "Saira", sans-serif;
  }
  .card {
    position: absolute; left: 196px; width: 720px; height: 412px;
    box-shadow: 0 6px 14px rgba(0,0,0,0.45);
  }
  .card--front { top: 146px; background: var(--card-white); }
  .card--back { top: 602px; background: var(--brand-red); }

  .wordmark {
    position: absolute; left: 0; right: 0;
    text-align: center; font-weight: 700; letter-spacing: 2px;
    text-transform: uppercase; line-height: 1;
  }
  .card--front .wordmark { top: 84px; font-size: 42px; color: var(--ink); }
  .card--back .wordmark { top: 160px; font-size: 62px; color: var(--card-white); }

  .contact { position: absolute; left: 0; right: 0; top: 204px; text-align: center; }
  .contact__name {
    color: var(--brand-red); font-weight: 700; font-size: 26px;
    letter-spacing: 0.5px; text-transform: uppercase; line-height: 1.2;
  }
  .contact__role { color: var(--ink); font-size: 19px; font-weight: 500; margin-top: 2px; }
  .contact__address { color: var(--muted); font-size: 18px; margin-top: 18px; }
  .contact__row {
    display: flex; justify-content: center; align-items: center; gap: 18px;
    color: var(--muted); font-size: 18px; margin-top: 2px; line-height: 1.5;
  }
  .contact__item { display: inline-flex; align-items: center; gap: 6px; }
  .icon { width: 16px; height: 16px; fill: var(--brand-red); flex: none; }

  .brand-row__name {
    position: absolute; top: 346px; transform: translateX(-50%);
    color: var(--card-white); font-size: 20px; font-weight: 500;
    white-space: nowrap; line-height: 1.3;
  }
  .brand-row__name--fen { left: 83px; }
  .brand-row__name--tava { left: 258px; }
  .brand-row__name--elm { left: 431px; }
  .brand-row__name--grit { left: 602px; }
</style>
</head>
<body>
  <section class="card card--front" aria-label="Card front">
    <div class="wordmark">Fen Athletics</div>
    <div class="contact">
      <p class="contact__name">Leo Pemberton-Hale</p>
      <p class="contact__role">Operations Manager</p>
      <p class="contact__address">Marsh Yard, Elmby, Thorne, YO9 4EX</p>
      <div class="contact__row">
        <span class="contact__item">
          <svg class="icon" viewBox="0 0 16 16" aria-hidden="true"><path d="M3.5 1l2.5 3-1.5 2c1 2 3 4 5 5l2-1.5 3 2.5-1.5 2.5C7 14 2 9 1 2.5z"/></svg>
          (+44) 1632 960 418
        </span>
        <span class="contact__item">
          <svg class="icon" viewBox="0 0 16 16" aria-hidden="true"><path d="M1 3h14v10H1z M1 3l7 6 7-6" stroke="#fff" stroke-width="1.2"/></svg>
          Leo@fenathletics.co.uk
        </span>
      </div>
      <div class="contact__row">
        <span class="contact__item">
          <svg class="icon" viewBox="0 0 16 16" aria-hidden="true"><circle cx="8" cy="8" r="7"/><path d="M4 6l3-2 2 2-2 3 3 3" stroke="#fff" stroke-width="1.3" fill="none"/></svg>
          www.fenathletics.co.uk
        </span>
      </div>
    </div>
  </section>

  <section class="card card--back" aria-label="Card back">
    <div class="wordmark">Fen Athletics</div>
    <span class="brand-row__name brand-row__name--fen">Fen</span>
    <span class="brand-row__name brand-row__name--tava">TavaPuni</span>
    <span class="brand-row__name brand-row__name--elm">ElmStretch</span>
    <span class="brand-row__name brand-row__name--grit">Grit and Rain</span>
  </section>
</body>
</html>
```